Advertising for school programs

We're wanting some advertising material for two new programs that we are running in 2022 and 2023. The programs are:
- Zenora Academic Enrichment Program
- Tidewell Athletic
Ideally we would like logos and advertising tiles for each that can be used across social media networks. It would be great to have simple advertising materials, that include the name of the program, a logo for each program, and some text that encourages people to apply.
We'd love to have designs with drawn students, so we don't have to use photos. I've included some photos and our school logo to assist.
A description of the programs is included below to help guide the design - You do not need to include ANY or ALL of the text below in the graphics, I have provided it for context.
A description of both programs below:
Zenora:
The Zenora Academic Enrichment Program is a differentiated pathway that caters specifically for highly capable students.
In the Zenora Academic Enrichment Pathway, students can learn and be assessed at a pace exceeding that of their current year level, with a focus on 21st Century Skills.
For information about the program and application packages, please see the zenora page of our website or contact Marnie Dowse Head of Department Junior School mdows41@brelvan.edu.au
Tidewell Athletic:
In 2022, we will be launching the Tidewell Athletic program to cater for our highly capable athletes.
Tallowmere has long been home to exceptional sporting talent, with multiple state and national representatives in a range of sports and year levels. Tidewell Athletic will provide a differentiated Health and Physical Education curriculum to ensure our student athletes benefit from the latest information on health, wellbeing, fitness and metal health.
The program is open to athletes from all sports and athletic pursuits, as the program is a holistic look at health and athletic performance.
Bursaries:

```html
<!DOCTYPE html>
<html lang="en">
<head>
<meta charset="utf-8">
<title>New Programs in 2022 &amp; 2023</title>
<link rel="stylesheet" href="https://fonts.googleapis.com/css2?family=Oswald:wght@500;600;700&family=Open+Sans:wght@400;600;700&display=swap">
<style>
  :root{
    --blue:#2f8fd6;
    --blue-light:#5fb0ea;
    --navy:#10345c;
    --ink:#2b3642;
    --paper:#ffffff;
    --bg:#eef1f4;
    --photo-a:#4a78a8;
    --photo-b:#9cc2e2;
  }
  *{box-sizing:border-box;margin:0;padding:0}
  html,body{width:727px;height:1200px;overflow:hidden;background:var(--bg)}
  body{font-family:"Open Sans",Arial,sans-serif;color:var(--ink)}
  .flyer{position:absolute;left:14px;top:96px;width:699px;height:988px;background:var(--paper);box-shadow:0 4px 16px rgba(0,0,0,.12);overflow:hidden}
  .flyer::before{content:"";position:absolute;left:0;top:0;width:100%;height:8px;background:var(--blue)}

  .hero-photo{position:absolute;right:0;top:8px;width:360px;height:322px;background:linear-gradient(135deg,var(--photo-b),var(--photo-a));}
  .hero-fade{position:absolute;right:200px;top:8px;width:160px;height:322px;background:linear-gradient(90deg,var(--paper),rgba(255,255,255,0))}
  .school-mark{position:absolute;right:60px;top:110px;display:flex;align-items:center;gap:10px}
  .school-mark .dot{width:34px;height:34px;border-radius:50%;background:var(--paper)}
  .school-mark .name{font-family:"Oswald",sans-serif;font-weight:600;font-size:26px;color:var(--paper);letter-spacing:1px}

  .headline{position:absolute;left:40px;top:40px;font-family:"Oswald",sans-serif;font-weight:700;color:var(--blue);text-transform:uppercase;line-height:1.02}
  .headline .big{font-size:64px;display:block}
  .headline .mid{font-size:44px;display:block}

  .programs-tag{position:absolute;left:0;top:210px;width:420px;height:32px;background:var(--blue);color:var(--paper);font-family:"Oswald",sans-serif;font-weight:600;font-size:17px;letter-spacing:1px;padding:5px 0 0 40px}
  .program-list{position:absolute;left:40px;top:254px;list-style:none;font-family:"Open Sans",sans-serif;font-weight:600;font-size:19px;color:var(--navy);line-height:1.6}
  .program-list li::before{content:"";display:inline-block;width:9px;height:9px;background:var(--blue);margin-right:12px;vertical-align:middle}

  .intro-band{position:absolute;left:0;top:338px;width:100%;height:64px;background:var(--navy);color:var(--paper);font-size:12.5px;line-height:1.5;padding:11px 40px}

  .col{position:absolute;top:428px;width:300px}
  .col-left{left:30px}
  .col-right{left:369px}
  .col h2{font-family:"Oswald",sans-serif;font-weight:600;font-size:24px;color:var(--blue);text-transform:uppercase;border-bottom:2px solid var(--blue);padding-bottom:6px;margin-bottom:14px}
  .col p{font-size:12px;line-height:1.6;margin-bottom:10px}
  .divider{position:absolute;left:349px;top:428px;width:1px;height:420px;background:#c9d7e4}

  .open-box{position:absolute;left:30px;top:720px;width:300px;height:186px;background:var(--blue);}
  .open-box p{position:absolute;left:16px;top:16px;width:150px;font-weight:700;font-size:14px;line-height:1.4;color:var(--paper)}
  .open-photo{position:absolute;right:0;bottom:0;width:130px;height:186px;background:linear-gradient(180deg,var(--photo-b),var(--photo-a))}

  .footer{position:absolute;left:0;bottom:0;width:100%;height:52px;background:var(--navy);display:flex;align-items:center;justify-content:space-around;padding:0 20px}
  .contact{display:flex;align-items:center;gap:10px;color:var(--paper);font-size:12.5px;font-weight:600}
  .contact svg{flex:none}
</style>
</head>
<body>
<main class="flyer">
  <div class="hero-photo" role="img" aria-label="Photo of a student studying, tinted blue"></div>
  <div class="hero-fade"></div>
  <div class="school-mark"><span class="dot"></span><span class="name">TALLOWMERE</span></div>

  <h1 class="headline"><span class="big">New</span><span class="mid">Programs in</span><span class="mid">2022 &amp; 2023</span></h1>

  <div class="programs-tag">THE PROGRAMS ARE:</div>
  <ul class="program-list">
    <li>Zenora Academic</li>
    <li>Enrichment Program</li>
  </ul>

  <div class="intro-band">Our school is proud to offer two new pathways that extend capable learners and athletes, building skills, confidence and wellbeing for every student who takes part.</div>

  <section class="col col-left">
    <h2>Zenora Academic</h2>
    <p>The Zenora Academic Enrichment Program is a differentiated pathway that caters specifically for highly capable students.</p>
    <p>In the Zenora Academic Enrichment Pathway, students can learn and be assessed at a pace exceeding that of their current year level, with a focus on 21st Century Skills.</p>
    <p>For information about the program and application packages, please see the zenora page of our website or contact Marnie Dowse, Head of Department Junior School, mdows41@brelvan.edu.au</p>
  </section>

  <div class="divider"></div>

  <section class="col col-right">
    <h2>Tidewell Athletic</h2>
    <p>In 2022, we will be launching the Tidewell Athletic program to cater for our highly capable athletes.</p>
    <p>Tallowmere has long been home to exceptional sporting talent, with multiple state and national representatives in a range of sports and year levels. Tidewell Athletic will provide a differentiated Health and Physical Education curriculum to ensure our student athletes benefit from the latest information on health, wellbeing, fitness and mental health.</p>
  </section>

  <div class="open-box">
    <p>Program is open to athletes from all sports and athletic pursuits, as the program is a holistic look at health and athletic performance.</p>
    <div class="open-photo" role="img" aria-label="Photo of a student reading at a desk"></div>
  </div>

  <footer class="footer">
    <div class="contact">
      <svg width="22" height="16" viewBox="0 0 22 16"><rect x="1" y="1" width="20" height="14" rx="2" fill="none" stroke="#5fb0ea" stroke-width="2"/><path d="M1 2l10 8 10-8" fill="none" stroke="#5fb0ea" stroke-width="2"/></svg>
      <span>mdows41@brelvan.edu.au</span>
    </div>
    <div class="contact">
      <svg width="22" height="16" viewBox="0 0 22 16"><rect x="1" y="1" width="20" height="14" rx="2" fill="none" stroke="#5fb0ea" stroke-width="2"/><path d="M1 2l10 8 10-8" fill="none" stroke="#5fb0ea" stroke-width="2"/></svg>
      <span>principal@tallowmereshs.edu.au</span>
    </div>
  </footer>
</main>
</body>
</html>
```